Corvana Tongue Works, LLC

We need a business card that includes information about our business and conveys a reliable business that provides document translation services and interpreters for a variety of corporate and individual clients. We want to come across as professional, reliable, yet approachable. It should include the following on one side:

ESL / ENL Language Classes, Private Lessons, and Online Tutors
PLEXA Training and Testing
Translating & Interpreting Services
Contact us about Over-the-Phone Interpreting in over 200 languages
24/7/365
www.corvanatongue.example

The other side should include (555) 481-3062

Rhoda Pelling, President
482 Garnet Ave., Ste. 219
Indianapolis, IN 40917

Please add USA as part of the address. Also, please add rmpelling@corvanatongueworks.example as the e-mail address. Thank you.

Target Market(s)

Business professionals, their families, the international community

Industry/Entity Type

Business

Contact Information for Business Card

24/7/365
www.corvanatongue.example

(555) 481-3062

Rhoda Pelling, President
482 Garnet Ave., Ste. 219
Indianapolis, IN 40917
USA

Font styles to use
Sans Serif

Colors

Designer to choose colors to be used in the design.

Requirements
Must have
• See project description
• e-mail address and web address
• Phone number
Nice to have
• a globe
• physical address
Should not have
• Should not have the same color scheme as other agencies in our market in Indiana unless it is blue and black. No purple or yellow.

```html
<!DOCTYPE html>
<html lang="en">
<head>
<meta charset="utf-8">
<title>Corvana Tongue Works, LLC — Business Card</title>
<link href="https://fonts.googleapis.com/css2?family=Roboto:wght@400;500&family=Roboto+Condensed:wght@400;700&display=swap" rel="stylesheet">
<style>
  :root {
    --bg: #2b2b2d;
    --ink: #1b1b1d;
    --paper: #ffffff;
    --blue: #2a93d5;
    --black: #0b0b0c;
  }
  * { box-sizing: border-box; margin: 0; padding: 0; }
  html, body {
    width: 1200px; height: 896px; overflow: hidden;
    background: var(--bg);
    font-family: "Roboto", Arial, sans-serif;
  }
  .canvas {
    position: relative; width: 1200px; height: 896px;
    display: flex; flex-direction: column; align-items: center; justify-content: center; gap: 40px;
  }
  .card {
    position: relative; width: 640px; height: 366px;
    border-radius: 22px; overflow: hidden;
  }

  /* Services side */
  .card--back { background: var(--black); color: var(--paper); }
  .card--back .brand { position: absolute; left: 96px; top: 40px; }
  .card--back .services {
    position: absolute; left: 40px; right: 40px; top: 160px;
    text-align: center; font-size: 17px; line-height: 1.3; font-weight: 500;
  }
  .card--back .rule {
    position: absolute; left: 40px; right: 40px; top: 250px;
    height: 2px; background: var(--blue);
  }
  .card--back .contact {
    position: absolute; left: 40px; right: 40px; top: 262px;
    text-align: center; font-size: 17px; line-height: 1.3; font-weight: 500;
  }

  /* Brand lockup */
  .brand { display: flex; align-items: center; gap: 16px; }
  .brand__dot { width: 88px; height: 88px; border-radius: 50%; background: var(--blue); flex: none; }
  .brand__name {
    font-family: "Roboto", Arial, sans-serif; font-weight: 400;
    font-size: 30px; line-height: 1.05;
  }
  .card--back .brand__name { color: var(--paper); }
  .card--front .brand__name { color: var(--ink); }

  /* Contact side */
  .card--front { background: var(--paper); color: var(--ink); }
  .card--front .brand { position: absolute; left: 34px; top: 40px; }
  .holder { position: absolute; right: 48px; top: 40px; text-align: right; }
  .holder__name {
    font-family: "Roboto Condensed", Arial, sans-serif; font-weight: 700;
    font-size: 34px; color: var(--blue); letter-spacing: 0.5px; text-transform: uppercase;
  }
  .holder__title { font-size: 16px; color: var(--ink); margin-top: 2px; }
  .edge-mark { position: absolute; right: 0; top: 40px; width: 22px; height: 40px; display: flex; }
  .edge-mark span:first-child { flex: 1; background: var(--blue); }
  .edge-mark span:last-child { width: 8px; background: var(--black); }
  .name-rule {
    position: absolute; left: 34px; right: 130px; top: 158px; height: 1.5px; background: var(--blue);
  }
  .address {
    position: absolute; right: 48px; top: 180px; text-align: right;
    font-size: 17px; line-height: 1.4;
  }
  .contact-list {
    position: absolute; left: 44px; bottom: 50px; list-style: none;
    font-size: 17px; line-height: 1.45;
  }
  .contact-list li { display: flex; align-items: center; gap: 10px; }
  .contact-list svg { width: 13px; height: 13px; flex: none; }
  .bottom-band { position: absolute; left: 0; right: 0; bottom: 0; height: 16px; display: flex; }
  .bottom-band span:first-child { width: 14px; background: var(--black); }
  .bottom-band span:last-child { flex: 1; background: var(--blue); }
</style>
</head>
<body>
<main class="canvas">

  <section class="card card--back" aria-label="Business card services side">
    <div class="brand">
      <span class="brand__dot"></span>
      <span class="brand__name">Corvana<br>Tongue Works<br>LLC</span>
    </div>
    <p class="services">
      ESL / ENL Language Classes, Private Lessons, and Online Tutors<br>
      PLEXA Training and Testing<br>
      Translating &amp; Interpreting Services
    </p>
    <div class="rule"></div>
    <p class="contact">
      Contact us about Over-the-Phone Interpreting in over 200 languages<br>
      24/7/365<br>
      www.corvanatongue.example
    </p>
  </section>

  <section class="card card--front" aria-label="Business card contact side">
    <div class="brand">
      <span class="brand__dot"></span>
      <span class="brand__name">Corvana<br>Tongue Works<br>LLC</span>
    </div>

    <div class="edge-mark"><span></span><span></span></div>
    <div class="holder">
      <p class="holder__name">Rhoda Pelling</p>
      <p class="holder__title">President</p>
    </div>
    <div class="name-rule"></div>

    <p class="address">482 Garnet Ave., Ste. 219<br>Indianapolis, IN 40917 USA</p>

    <ul class="contact-list">
      <li>
        <svg viewBox="0 0 24 24" aria-hidden="true"><path fill="#2a93d5" d="M6.6 10.8a15 15 0 0 0 6.6 6.6l2.2-2.2a1 1 0 0 1 1-.25 11.4 11.4 0 0 0 3.6.57 1 1 0 0 1 1 1V20a1 1 0 0 1-1 1A17 17 0 0 1 3 4a1 1 0 0 1 1-1h3.5a1 1 0 0 1 1 1c0 1.25.2 2.45.57 3.6a1 1 0 0 1-.25 1z"/></svg>
        (555) 481-3062
      </li>
      <li>
        <svg viewBox="0 0 24 24" aria-hidden="true"><rect x="2" y="5" width="20" height="14" rx="2" fill="#2a93d5"/><path d="M3 6l9 7 9-7" fill="none" stroke="#fff" stroke-width="2"/></svg>
        rmpelling@corvanatongueworks.example
      </li>
      <li>
        <svg viewBox="0 0 24 24" aria-hidden="true"><circle cx="12" cy="12" r="10" fill="#2a93d5"/><path d="M2 12h20M12 2c3 3 3 17 0 20M12 2c-3 3-3 17 0 20" fill="none" stroke="#fff" stroke-width="1.5"/></svg>
        www.corvanatongue.example
      </li>
    </ul>

    <div class="bottom-band"><span></span><span></span></div>
  </section>

</main>
</body>
</html>
```